Website for new crypto research organization

See brief (attached). This is a pretty basic website with only a handful of pages + ability to collect email addresses.

```html
<!DOCTYPE html>
<html lang="en">
<head>
<meta charset="utf-8">
<title>Seaglass Digital</title>
<link href="https://fonts.googleapis.com/css2?family=Roboto:wght@400;500;700;900&display=swap" rel="stylesheet">
<style>
:root{
  --accent:#1e9ccc;
  --accent-dark:#1886b3;
  --teal:#1a9e9a;
  --ink:#111111;
  --body:#333333;
  --hero-deep:#07182a;
  --hero-mid:#0d2f4c;
  --tint-a:#edfcfe;
  --tint-b:#e2f6fc;
  --footer:#07131d;
  --white:#ffffff;
  --line:#e3e3e3;
}
*{margin:0;padding:0;box-sizing:border-box}
html,body{width:1200px;height:3000px;overflow:hidden}
body{position:relative;font-family:'Roboto',Arial,sans-serif;color:var(--body);background:var(--white)}
.abs{position:absolute}
a{text-decoration:none;color:inherit}

/* hero */
.hero{position:absolute;left:0;top:0;width:1200px;height:704px;
  background:radial-gradient(ellipse at 75% 35%,#1b4f7a 0%,var(--hero-mid) 35%,var(--hero-deep) 75%)}
.brand{position:absolute;display:flex;align-items:center;justify-content:center;color:var(--accent);font-weight:700;letter-spacing:.5px}
.brand-top{left:111px;top:18px;width:139px;height:80px;font-size:17px}
.nav{position:absolute;left:319px;top:46px;display:flex;gap:0;font-size:16px;color:var(--white)}
.nav a{position:absolute;white-space:nowrap}
.nav .active{color:var(--accent)}
.nav .active::after{content:"";position:absolute;left:0;right:0;top:27px;height:2px;background:var(--accent)}
.btn{position:absolute;background:var(--accent);color:var(--white);font-weight:500;display:flex;align-items:center;justify-content:center;gap:8px;border-radius:3px}
.login{left:975px;top:35px;width:114px;height:47px;font-size:16px}
.hero-title{left:111px;top:268px;color:var(--white);font-weight:700;line-height:1.25}
.hero-title .small{font-size:35px;display:block}
.hero-title .big{font-size:43px;display:block;margin-top:8px}
.hero-text{left:111px;top:380px;width:460px;color:var(--white);font-size:16px;line-height:26px}
.start{left:111px;top:454px;width:153px;height:47px;font-size:16px}
.dots{left:1140px;top:327px}
.dots span{display:block;width:20px;height:20px;border-radius:50%;background:var(--white);margin-bottom:14px}
.dots .on{background:var(--teal)}

/* about */
.about-frame{left:128px;top:804px;width:416px;height:405px;background:var(--accent)}
.about-photo{left:111px;top:790px;width:419px;height:406px;background:linear-gradient(160deg,#7d7564 0%,#3a3530 40%,#4b3b45 70%,#1c1a1d 100%)}
.h2{font-size:34px;font-weight:700;color:var(--ink)}
.about-title{left:597px;top:805px}
.about-title::after{content:"";display:block;width:60px;height:3px;background:var(--accent);margin-top:6px}
.about-text{left:597px;top:871px;width:490px;font-size:16px;line-height:25.7px;color:var(--body)}
.more{position:absolute;color:var(--accent);font-weight:500;font-size:17px;display:flex;align-items:center;gap:8px}

/* pillars */
.pillar{position:absolute;top:1295px;height:346px;width:400px;text-align:center}
.pillar h3{font-size:22px;font-weight:700;color:var(--ink);margin-bottom:12px}
.pillar p{font-size:16px;line-height:25.7px;color:var(--body);margin:0 auto}

/* newsletter */
.news-band{left:0;top:1641px;width:1200px;height:287px;background:linear-gradient(100deg,#1a8fb8 0%,#2296bd 40%,#1a9aa0 80%,#12918a 100%)}
.news-title{left:0;top:1689px;width:1200px;text-align:center;color:var(--white);font-size:35px;font-weight:700}
.news-text{left:240px;top:1752px;width:720px;text-align:center;color:var(--white);font-size:16px;line-height:26px}
.field{position:absolute;top:1827px;height:44px;width:242px;background:var(--white);border-radius:2px;font-size:14px;color:#555;padding:14px 14px;line-height:16px}
.submit{position:absolute;left:912px;top:1827px;width:138px;height:44px;border:2px solid var(--white);border-radius:3px;color:var(--white);font-weight:700;font-size:16px;display:flex;align-items:center;justify-content:center}

/* news */
.news-heading{left:0;top:2005px;width:1200px;text-align:center}
.card{position:absolute;top:2083px;width:313px;height:379px;border:1px solid var(--line);box-shadow:0 0 4px rgba(0,0,0,.08);padding:30px 22px}
.author{display:flex;align-items:center;gap:18px;font-weight:500;font-size:16px;color:var(--ink)}
.avatar{width:40px;height:40px;border-radius:50%;background:linear-gradient(#9aa7b2,#5f6b75)}
.card h4{margin-top:20px;font-size:17.5px;font-weight:500;color:var(--ink);line-height:22px;letter-spacing:.2px}
.meta{display:flex;gap:28px;margin-top:14px;font-size:14px;color:var(--accent);font-weight:500}
.meta span{display:flex;align-items:center;gap:7px}
.card p{margin-top:14px;font-size:16px;line-height:25.7px;color:var(--body)}
.card .more{position:static;margin-top:14px}
.report{left:481px;top:2505px;width:238px;height:48px;font-size:16px}

/* footer */
.footer{left:0;top:2633px;width:1200px;height:367px;background:var(--footer)}
.brand-foot{left:111px;top:2693px;width:179px;height:100px;font-size:22px}
.foot-text{left:111px;top:2823px;width:260px;color:var(--white);font-size:16px;line-height:26px}
.foot-h{position:absolute;top:2688px;color:var(--white);font-weight:700;font-size:16px}
.foot-item{position:absolute;color:var(--white);font-size:16px;display:flex;align-items:center;gap:14px;line-height:26px}
.divider{left:111px;top:2950px;width:978px;height:1px;background:#34414b}
.copy{left:0;top:2967px;width:1200px;text-align:center;color:var(--white);font-size:14px}
</style>
</head>
<body>

<header class="hero" role="img" aria-label="Dark blue background image of a glowing digital network of connected nodes"></header>
<div class="brand brand-top">SEAGLASS</div>
<nav class="nav">
  <a class="active" style="left:0">HOME</a>
  <a style="left:79px">ABOUT US</a>
  <a style="left:196px">RESEARCH</a>
  <a style="left:317px">NEWS</a>
  <a style="left:406px">CAREERS</a>
  <a style="left:514px">CONTACT</a>
</nav>
<a class="btn login">LOGIN
  <svg width="13" height="14" viewBox="0 0 13 14"><circle cx="6.5" cy="4" r="3.5" fill="#fff"/><path d="M0 14c0-4 3-6 6.5-6s6.5 2 6.5 6z" fill="#fff"/></svg>
</a>
<h1 class="abs hero-title"><span class="small">WELCOME TO</span><span class="big">SEAGLASS DIGITAL</span></h1>
<p class="abs hero-text">Lorem ipsum dolor sit amet, consectetur adipiscing elit, sed do eiusmod tempor incididunt ut labore et dolore magna aliqua.</p>
<a class="btn start">GET STARTED
  <svg width="14" height="14" viewBox="0 0 14 14"><circle cx="7" cy="7" r="7" fill="#fff"/><path d="M5.5 4l3 3-3 3" stroke="#1e9ccc" stroke-width="2" fill="none"/></svg>
</a>
<div class="abs dots"><span></span><span></span><span class="on"></span><span></span></div>

<section>
  <div class="abs about-frame"></div>
  <div class="abs about-photo" role="img" aria-label="Photo of an underground tunnel covered in colourful graffiti"></div>
  <h2 class="abs h2 about-title">ABOUT US</h2>
  <p class="abs about-text">Lorem ipsum dolor sit amet, consectetur adipiscing elit, sed eiusmod tempor incididunt ut labore et dolore magna aliqua.Uirt enim ad minim veniam,bquis nostrud exercitation ullamco laboris aliqua aliquip exibea commodo consequat.Duis aute irure dolor in reprehenderit in voluptate velit esse cillum dolore eu fugiat nulla pariatur.Excepteur sint occaecat non proident,sunt in culpa qui officia deserunt mollit anim est laborum. Lorem ipsum dolor sit amet, consectetur adipiscing elit, sed&nbsp; eiusmod tempor incididunt labore dolore magna aliqunim ad minim veniam quis nostrud exercitation ullamco laboris nisi aliquip&nbsp; commodo consequat. Duis aute irure dolor in reprehenderit in voluptate velit esse cillum dolre eu fugiat nulla pariatur Excepteur sint occaecat cupidatat .</p>
  <a class="more" style="left:597px;top:1173px">LEARN MORE
    <svg width="50" height="16" viewBox="0 0 50 16"><path d="M0 8h46M41 2l6 6-6 6" stroke="#1e9ccc" stroke-width="2" fill="none"/></svg>
  </a>
</section>

<section>
  <div class="pillar" style="left:0;background:var(--tint-a)">
    <svg style="margin-top:55px" width="100" height="84" viewBox="0 0 100 84">
      <g stroke="#1a9e9a" stroke-width="5" stroke-linecap="round"><path d="M50 2v8M30 6l4 7M70 6l-4 7M14 14l6 6M86 14l-6 6"/></g>
      <path d="M2 42C20 20 80 20 98 42 80 64 20 64 2 42z" fill="#1a9e9a"/>
      <circle cx="50" cy="42" r="16" fill="#edfcfe"/><circle cx="50" cy="42" r="9" fill="#1a9e9a"/><circle cx="50" cy="42" r="4" fill="#edfcfe"/>
      <path d="M62 52l20 22" stroke="#1a9e9a" stroke-width="9" stroke-linecap="round"/>
    </svg>
    <h3 style="margin-top:6px">VISION</h3>
    <p style="width:290px">Web3, blockchain technology, and digital assets will drive the largest wealth shift in the global economy since the advent of the internet.</p>
  </div>
  <div class="pillar" style="left:400px;background:var(--tint-b)">
    <svg style="margin-top:82px" width="132" height="82" viewBox="0 0 132 82">
      <g fill="#1e9ccc"><circle cx="66" cy="16" r="15"/><circle cx="24" cy="28" r="11"/><circle cx="108" cy="28" r="11"/>
      <path d="M38 82v-20c0-16 12-26 28-26s28 10 28 26v20z"/><path d="M0 78v-14c0-12 9-18 22-18 6 0 11 1 15 4-3 4-5 9-5 14v14z"/><path d="M132 78v-14c0-12-9-18-22-18-6 0-11 1-15 4 3 4 5 9 5 14v14z"/></g>
    </svg>
    <h3 style="margin-top:14px">WHO WE ARE</h3>
    <p style="width:290px">A thematic, research-driven digital asset investment firm built for founders.</p>
  </div>
  <div class="pillar" style="left:800px;background:var(--tint-a)">
    <svg style="margin-top:58px" width="82" height="82" viewBox="0 0 82 82">
      <circle cx="41" cy="41" r="35" fill="none" stroke="#1a9e9a" stroke-width="9"/>
      <circle cx="41" cy="41" r="18" fill="none" stroke="#1a9e9a" stroke-width="8"/>
      <circle cx="41" cy="41" r="5" fill="#1a9e9a"/>
      <path d="M41 41L12 12" stroke="#1a9e9a" stroke-width="6" stroke-linecap="round"/>
      <path d="M6 18l4-14 6 8 8 6-14 4z" fill="#1a9e9a"/>
    </svg>
    <h3 style="margin-top:10px">MISSION</h3>
    <p style="width:330px">We apply a principled digital asset investment strategy and partner with founders to enable their token-based decentralized networks to scale globally.</p>
  </div>
</section>

<section>
  <div class="abs news-band"></div>
  <h2 class="abs news-title">OUR NEWSLETTER</h2>
  <p class="abs news-text">Lorem ipsum dolor sit amet, consectetur adipiscing elit, sed do eiusmod tempor incididunt ut labore et dolore magna aliqua. Ut enim ad minim veniam, quis nostrud exercitation ullamco laboris nisi</p>
  <div class="field" style="left:149px">Enter Name:</div>
  <div class="field" style="left:403px">Enter Email:</div>
  <div class="field" style="left:657px">Enter Adrees:</div>
  <a class="submit">SUBMIT</a>
</section>

<section>
  <h2 class="abs h2 news-heading">OUR NEWS</h2>
  <article class="card" style="left:114px">
    <div class="author"><div class="avatar" role="img" aria-label="Author portrait"></div>MARA VOSS</div>
    <h4>LOREM DOLOR&nbsp; CONSECTETUR SIT ADIPISCING ELIT DO DOLOR</h4>
    <div class="meta"><span><svg width="14" height="12" viewBox="0 0 14 12"><ellipse cx="7" cy="5" rx="7" ry="5" fill="#1a9e9a"/><path d="M2 8l-1 4 4-2z" fill="#1a9e9a"/></svg>2 Comments</span><span><svg width="13" height="13" viewBox="0 0 13 13"><rect x="1" y="2" width="11" height="10" fill="none" stroke="#1e9ccc" stroke-width="1.5"/><path d="M1 5h11M4 0v3M9 0v3" stroke="#1e9ccc" stroke-width="1.5"/></svg>Feb 9,2022</span></div>
    <p>Lorem ipsum dolor&nbsp; amet consectetur adipiscing elit sed do eiusmod tempor incididunt labore dolore magna aliqua magna aliqua admin magna ut&nbsp; minim veniamquis nostrud exercitation.</p>
    <a class="more">LEARN MORE <svg width="50" height="16" viewBox="0 0 50 16"><path d="M0 8h46M41 2l6 6-6 6" stroke="#1e9ccc" stroke-width="2" fill="none"/></svg></a>
  </article>
  <article class="card" style="left:444px">
    <div class="author"><div class="avatar" role="img" aria-label="Author portrait" style="background:linear-gradient(#c9b49c,#8a6e55)"></div>ILAN BROOK</div>
    <h4>LOREM DOLOR&nbsp; CONSECTETUR SIT ADIPISCING ELIT DO DOLOR</h4>
    <div class="meta"><span><svg width="14" height="12" viewBox="0 0 14 12"><ellipse cx="7" cy="5" rx="7" ry="5" fill="#1a9e9a"/><path d="M2 8l-1 4 4-2z" fill="#1a9e9a"/></svg>2 Comments</span><span><svg width="13" height="13" viewBox="0 0 13 13"><rect x="1" y="2" width="11" height="10" fill="none" stroke="#1e9ccc" stroke-width="1.5"/><path d="M1 5h11M4 0v3M9 0v3" stroke="#1e9ccc" stroke-width="1.5"/></svg>Feb 9,2022</span></div>
    <p>Lorem ipsum dolor&nbsp; amet consectetur adipiscing elit sed do eiusmod tempor incididunt labore dolore magna aliqua magna aliqua admin magna ut&nbsp; minim veniamquis nostrud exercitation.</p>
    <a class="more">LEARN MORE <svg width="50" height="16" viewBox="0 0 50 16"><path d="M0 8h46M41 2l6 6-6 6" stroke="#1e9ccc" stroke-width="2" fill="none"/></svg></a>
  </article>
  <article class="card" style="left:774px">
    <div class="author"><div class="avatar" role="img" aria-label="Author portrait" style="background:linear-gradient(#b9cde0,#6b8aa8)"></div>TESS MARLOW</div>
    <h4>LOREM DOLOR&nbsp; CONSECTETUR SIT ADIPISCING ELIT DO DOLOR</h4>
    <div class="meta"><span><svg width="14" height="12" viewBox="0 0 14 12"><ellipse cx="7" cy="5" rx="7" ry="5" fill="#1a9e9a"/><path d="M2 8l-1 4 4-2z" fill="#1a9e9a"/></svg>2 Comments</span><span><svg width="13" height="13" viewBox="0 0 13 13"><rect x="1" y="2" width="11" height="10" fill="none" stroke="#1e9ccc" stroke-width="1.5"/><path d="M1 5h11M4 0v3M9 0v3" stroke="#1e9ccc" stroke-width="1.5"/></svg>Feb 9,2022</span></div>
    <p>Lorem ipsum dolor&nbsp; amet consectetur adipiscing elit sed do eiusmod tempor incididunt labore dolore magna aliqua magna aliqua admin magna ut&nbsp; minim veniamquis nostrud exercitation.</p>
    <a class="more">LEARN MORE <svg width="50" height="16" viewBox="0 0 50 16"><path d="M0 8h46M41 2l6 6-6 6" stroke="#1e9ccc" stroke-width="2" fill="none"/></svg></a>
  </article>
  <a class="btn report">RECENT RESEARCH REPORT</a>
</section>

<footer>
  <div class="abs footer"></div>
  <div class="brand brand-foot">SEAGLASS</div>
  <p class="abs foot-text">Lorem ipsum dolor sit amet, consectetur adipiscing elit, sed do eiusmod tempor incididunt ut</p>

  <h3 class="foot-h" style="left:448px">CONTACT US</h3>
  <div class="foot-item" style="left:448px;top:2731px"><svg width="16" height="16" viewBox="0 0 16 16"><path d="M3 1l3 3-2 2c1 2 3 4 6 6l2-2 3 3-2 2C7 15 1 9 1 3z" fill="#fff"/></svg> + 555 (0142) 310</div>
  <div class="foot-item" style="left:448px;top:2784px"><svg width="16" height="12" viewBox="0 0 16 12"><rect width="16" height="12" rx="1" fill="#fff"/><path d="M0 1l8 6 8-6" stroke="#07131d" stroke-width="1.5" fill="none"/></svg> info@seaglassdigital.com</div>
  <div class="foot-item" style="left:448px;top:2837px"><svg width="12" height="16" viewBox="0 0 12 16"><path d="M6 16C2 10 0 8 0 6a6 6 0 0112 0c0 2-2 4-6 10z" fill="#fff"/><circle cx="6" cy="6" r="2" fill="#07131d"/></svg><span style="width:190px;text-align:center">23,Lorem ipsum dolor sit consectetur adipiscing elit, sed do amet ut eiusmod</span></div>

  <h3 class="foot-h" style="left:784px">QUICKLINKS</h3>
  <div class="foot-item" style="left:784px;top:2725px">Home</div>
  <div class="foot-item" style="left:784px;top:2760px">About</div>
  <div class="foot-item" style="left:784px;top:2795px">Research</div>
  <div class="foot-item" style="left:784px;top:2830px">News</div>
  <div class="foot-item" style="left:784px;top:2865px">Careers</div>
  <div class="foot-item" style="left:784px;top:2900px">Contact</div>

  <h3 class="foot-h" style="left:984px">FOLLOW US</h3>
  <div class="foot-item" style="left:984px;top:2725px"><svg width="14" height="14"><rect width="14" height="14" fill="#fff"/></svg> Feedhall</div>
  <div class="foot-item" style="left:984px;top:2771px"><svg width="14" height="14"><circle cx="7" cy="7" r="7" fill="#fff"/></svg> Chirpline</div>
  <div class="foot-item" style="left:984px;top:2817px"><svg width="14" height="14"><rect width="14" height="14" fill="#fff"/></svg> Snapframe</div>
  <div class="foot-item" style="left:984px;top:2863px"><svg width="14" height="14"><circle cx="7" cy="7" r="7" fill="#fff"/></svg> Reelcast</div>

  <div class="abs divider"></div>
  <p class="abs copy">©Copyrights 2022 Seaglass Digital&nbsp;&nbsp; All Rights Reserved.</p>
</footer>

</body>
</html>
```